I'm looking for a smart new design for business cards

Industry/Entity Type

Commercial Electrical

Contact Information for Business Card

Logo, name, email, position, website QR

Requirements
Nice to have
• Logo embedded behind the text side

```html
<!DOCTYPE html>
<html lang="en">
<head>
<meta charset="utf-8">
<title>Voltline Commercial Services – Business Card</title>
<link href="https://fonts.googleapis.com/css2?family=Montserrat:wght@400;500;700&display=swap" rel="stylesheet">
<style>
  :root {
    --backdrop: #9a9a9a;
    --navy: #2a2a72;
    --red: #e21e2d;
    --white: #ffffff;
    --ink: #333333;
    --card-w: 715px;
    --card-h: 409px;
    --card-r: 30px;
  }
  * { box-sizing: border-box; margin: 0; padding: 0; }
  html, body {
    width: 1200px; height: 1108px; overflow: hidden;
    background: var(--backdrop);
    font-family: "Montserrat", sans-serif;
  }
  .canvas { position: relative; width: 1200px; height: 1108px; }
  .card {
    position: absolute; left: 242px;
    width: var(--card-w); height: var(--card-h);
    border-radius: var(--card-r); overflow: hidden;
  }
  .card--front { top: 119px; background: var(--navy); }
  .card--back  { top: 581px; background: var(--white); }

  /* Front */
  .front-brand {
    position: absolute; inset: 0;
    display: flex; flex-direction: column; align-items: center; justify-content: center;
    color: var(--white); font-weight: 700; text-align: center;
  }
  .front-brand__name { font-size: 78px; letter-spacing: 4px; line-height: 1; }
  .front-brand__tag { font-size: 30px; letter-spacing: 2px; margin-top: 22px; line-height: 1.2; }

  /* Back */
  .back-brand {
    position: absolute; left: 40px; top: 130px; width: 315px;
    display: flex; flex-direction: column; align-items: center;
    color: var(--navy); font-weight: 700; text-align: center;
  }
  .back-brand__mark { width: 30px; height: 30px; background: var(--red); margin-bottom: 16px; }
  .back-brand__name { font-size: 42px; letter-spacing: 2px; line-height: 1; }
  .back-brand__tag { font-size: 17px; letter-spacing: 1px; margin-top: 12px; line-height: 1.3; }

  .divider {
    position: absolute; left: 371px; top: 118px;
    width: 2px; height: 172px; background: var(--red);
  }
  .contact { position: absolute; left: 401px; top: 108px; }
  .contact__name { font-size: 33px; font-weight: 700; color: var(--navy); line-height: 1.1; }
  .contact__name span { color: var(--red); }
  .contact__role { font-size: 19px; font-weight: 500; color: var(--ink); margin-top: 6px; }
  .contact__list { list-style: none; margin-top: 36px; }
  .contact__item {
    display: flex; align-items: center; gap: 8px;
    font-size: 19px; color: var(--ink); height: 28.5px;
  }
  .contact__icon { width: 16px; height: 16px; fill: var(--red); flex: none; }
</style>
</head>
<body>
<div class="canvas">
  <section class="card card--front">
    <div class="front-brand">
      <div class="front-brand__name">VOLTLINE</div>
      <div class="front-brand__tag">COMMERCIAL SERVICES</div>
    </div>
  </section>

  <section class="card card--back">
    <div class="back-brand">
      <div class="back-brand__mark"></div>
      <div class="back-brand__name">VOLTLINE</div>
      <div class="back-brand__tag">COMMERCIAL SERVICES</div>
    </div>

    <div class="divider"></div>

    <div class="contact">
      <div class="contact__name">Daniel <span>Hartley</span></div>
      <div class="contact__role">Managing Director</div>
      <ul class="contact__list">
        <li class="contact__item">
          <svg class="contact__icon" viewBox="0 0 16 16" aria-hidden="true"><path d="M1 6c0-2 3-3.5 7-3.5S15 4 15 6v1.3h-3.2V5.6C10.6 5.2 5.4 5.2 4.2 5.6v1.7H1zM3.5 8.2 5.5 6.5h5l2 1.7V13h-9z"/></svg>
          123 456 780
        </li>
        <li class="contact__item">
          <svg class="contact__icon" viewBox="0 0 16 16" aria-hidden="true"><path d="M1 3.5h14v9H1zm1.5 1.3v.4L8 9l5.5-3.8v-.4zM2.5 7v4.2h11V7L8 10.8z"/></svg>
          info@voltlinecs.com
        </li>
        <li class="contact__item">
          <svg class="contact__icon" viewBox="0 0 16 16" aria-hidden="true"><circle cx="8" cy="8" r="7"/><path d="M4 5.5c1.5-.5 2.5.5 2 1.8-.4 1.2.8 1.6.6 3-.2 1-1.2 1.4-1.8 2.5M10 2.5c-.5 1.5.8 2.2 2 2.3 1 .1 1.5 1.4 1 2.8" stroke="#fff" stroke-width="1.2" fill="none"/></svg>
          www.voltlinecs.com
        </li>
      </ul>
    </div>
  </section>
</div>
</body>
</html>
```